Velmora Systems Website

Website design for our company: Velmora Systems.
The website should look fresh and IT focused. Please have a look at http://www.velmorasystems.example.au/ for our current design. We want something fresh and new, professional looking, in WordPress so we can easily make changes.

It Company

```html
<!DOCTYPE html>
<html lang="en">
<head>
<meta charset="utf-8">
<title>Velmora Systems</title>
<link href="https://fonts.googleapis.com/css2?family=Open+Sans:wght@400;600;700&family=Arimo:wght@400;700&display=swap" rel="stylesheet">
<style>
:root{
  --green:#0aa84f;
  --blue:#0d6fc2;
  --blue-dark:#0e3a66;
  --ink:#333;
  --grey:#8a8a8a;
  --hero:#0b1628;
  --panel:#eeeeee;
  --btn:#2a2a2a;
}
*{margin:0;padding:0;box-sizing:border-box}
html,body{width:960px;height:1200px;overflow:hidden}
body{position:relative;background:#fff;font-family:"Arimo",Arial,sans-serif;color:var(--ink)}

/* header */
.site-header{position:absolute;left:0;top:0;width:960px;height:94px;background:linear-gradient(#fff,#ececec);border-top:2px solid var(--blue)}
.brand{position:absolute;left:142px;top:30px;display:flex;align-items:center;gap:8px;font-family:"Open Sans",sans-serif;font-weight:700;font-size:19px;color:var(--green)}
.brand-dot{width:22px;height:22px;border-radius:50%;background:var(--green)}
.search{position:absolute;left:524px;top:22px;width:148px;height:22px;border:1px solid #ccc;background:#fff;font:italic 9px "Arimo",sans-serif;color:#555;padding:6px 6px}
.search svg{position:absolute;right:6px;top:5px}
.call{position:absolute;left:694px;top:18px}
.call-label{position:absolute;left:30px;top:1px;font:9px "Open Sans",sans-serif;color:#444;white-space:nowrap}
.call-num{position:absolute;left:30px;top:11px;font:15px "Open Sans",sans-serif;color:#222;white-space:nowrap}
.main-nav{position:absolute;left:316px;top:62px;display:flex;align-items:center;font:600 10.5px "Open Sans",sans-serif;color:#333}
.main-nav a{color:inherit;text-decoration:none;padding:0 12px;border-left:1px solid #bbb;line-height:12px}
.main-nav a.active{background:var(--green);color:#fff;padding:4px 9px;border:0;line-height:11px}
.main-nav a.active + a{border-left:0}

/* hero */
.hero{position:absolute;left:0;top:94px;width:960px;height:336px;background:var(--hero)}
.hero-photo{position:absolute;left:142px;top:0;width:676px;height:336px;background:linear-gradient(100deg,#4d5560 0%,#8c9299 35%,#c3c7cb 60%,#5c636b 100%)}
.hero-arrow{position:absolute;top:142px;width:28px;height:28px;border-radius:50%;background:#111;display:flex;align-items:center;justify-content:center}
.hero-caption{position:absolute;left:0;top:299px;width:818px;height:37px;background:rgba(16,100,178,.88);color:#fff;font:19px "Open Sans",sans-serif;text-align:center;line-height:37px;padding-left:38px}

/* services */
.services{position:absolute;left:0;top:430px;width:960px;height:224px;background:var(--green)}
.section-title{position:absolute;font:600 17px "Open Sans",sans-serif}
.services .section-title{left:144px;top:19px;color:#fff}
.services-rule{position:absolute;left:142px;top:43px;width:676px;height:1px;background:rgba(255,255,255,.6)}
.pager{position:absolute;display:flex;gap:10px}
.service-card{position:absolute;top:65px;width:126px;height:127px;background:var(--blue);border-radius:3px;text-align:center}
.service-icon{position:absolute;left:14px;top:14px;width:98px;height:74px;border-radius:50%;background:radial-gradient(#fff 60%,#e4e4e4);display:flex;align-items:center;justify-content:center;box-shadow:0 1px 2px rgba(0,0,0,.3)}
.service-label{position:absolute;left:0;right:0;top:105px;font:700 11px "Open Sans",sans-serif;color:#fff}
.band-shadow{position:absolute;left:120px;top:654px;width:720px;height:14px;background:radial-gradient(ellipse at top,rgba(0,0,0,.35),rgba(0,0,0,0) 70%)}

/* info panels */
.panel{position:absolute;top:701px;width:211px;height:219px;background:linear-gradient(#fafafa,#e9e9e9)}
.panel-head{height:29px;background:var(--blue);color:#fff;font:600 17px "Open Sans",sans-serif;padding:3px 6px}
.panel-shadow{position:absolute;top:920px;width:211px;height:10px;background:radial-gradient(ellipse at top,rgba(0,0,0,.3),rgba(0,0,0,0) 70%)}
.about-photo{position:absolute;left:6px;top:33px;width:202px;height:94px;background:linear-gradient(90deg,#c9d3dc,#8e9aa8 50%,#3b4350)}
.about-text{position:absolute;left:6px;top:136px;width:202px;font-size:8.5px;line-height:12.8px;text-align:justify;color:#333}
.tab-btn{position:absolute;top:201px;height:19px;background:var(--btn);color:#fff;font:700 9px "Arimo",sans-serif;line-height:19px;text-align:center;clip-path:polygon(10px 0,calc(100% - 10px) 0,100% 100%,0 100%)}
.quote{position:absolute;left:6px;width:196px;font-size:8.8px;line-height:14px;color:#333;white-space:nowrap}
.quote-by{position:absolute;right:7px;text-align:right;font-weight:700;font-size:8.5px;line-height:10.5px;white-space:nowrap}
.q{font-family:Georgia,serif;color:#999;font-size:13px;line-height:0}
.field{position:absolute;left:6px;width:204px;height:20px;background:#fff;border:1px solid #ccc;font:italic 8.5px "Arimo",sans-serif;color:#666;padding:4px 8px}

/* clients */
.clients-title{left:142px;top:952px;color:var(--blue)}
.rule{position:absolute;height:1px;background:#bbb}
.client{position:absolute;top:1000px;display:flex;align-items:center;gap:5px;font:700 16px "Open Sans",sans-serif;color:#555}
.client i{display:block;width:12px;height:12px;background:#888}
.remote-title{left:609px;top:952px;color:var(--blue)}
.connect{position:absolute;left:609px;top:1013px;width:81px;height:18px;background:var(--btn);color:#fff;font:10px "Open Sans",sans-serif;line-height:18px;text-align:center}

/* footer */
.site-footer{position:absolute;left:0;top:1056px;width:960px;height:144px;background:var(--blue-dark);border-top:2px solid var(--green);color:#fff}
.foot-title{position:absolute;top:10px;font:13px "Open Sans",sans-serif;padding-bottom:5px;border-bottom:1px dotted #6d8aa8}
.quick-links{position:absolute;left:146px;top:36px;list-style:none;font-size:9.5px;line-height:14.5px}
.quick-links li::before{content:"›";color:#8aa;margin-right:7px}
.news-text{position:absolute;left:286px;top:40px;width:150px;font-size:8px;line-height:14px}
.news-input{position:absolute;left:286px;top:88px;width:108px;height:20px;background:#fff;color:#888;font-size:8px;padding:5px 6px}
.news-btn{position:absolute;left:395px;top:88px;width:43px;height:20px;background:#222;font-size:9.5px;text-align:center;line-height:20px}
.contact-row{position:absolute;left:478px;display:flex;gap:9px;align-items:flex-start;font-size:9.5px;line-height:15px}
.foot-brand{position:absolute;left:670px;top:28px;display:flex;align-items:center;gap:7px;font:700 15px "Open Sans",sans-serif;color:#fff}
.follow{position:absolute;left:698px;top:88px;font:600 10.5px "Open Sans",sans-serif}
.social{position:absolute;left:697px;top:107px;display:flex;gap:6px}
.social i{display:block;width:13px;height:13px;background:#fff;border-radius:2px}
</style>
</head>
<body>

<header class="site-header">
  <div class="brand"><span class="brand-dot"></span>Velmora Systems</div>
  <div class="search">search
    <svg width="11" height="11" viewBox="0 0 11 11"><circle cx="4.5" cy="4.5" r="3.5" fill="none" stroke="#888" stroke-width="1.3"/><line x1="7" y1="7" x2="10" y2="10" stroke="#888" stroke-width="1.5"/></svg>
  </div>
  <div class="call">
    <svg width="26" height="26" viewBox="0 0 26 26"><circle cx="13" cy="13" r="11.5" fill="none" stroke="#0aa84f" stroke-width="1.5"/><path d="M10 7c-2 1-2 3-1 6s3 5 5 6c1 .5 2 0 3-1l-2-2-1.5 1c-1-.5-2.5-2.5-3-4l1-1.5z" fill="#0aa84f"/></svg>
    <span class="call-label">Call Us Today</span>
    <span class="call-num">123 456 7890</span>
  </div>
  <nav class="main-nav">
    <a class="active">HOME</a><a>ABOUT US</a><a>SERVICES</a><a>SUPPORT</a><a>TESTIMONIALS</a><a>CLIENTS</a><a>CONTACT US</a>
  </nav>
</header>

<section class="hero">
  <div class="hero-photo" role="img" aria-label="Engineer working on a laptop beside server racks in a data centre"></div>
  <div class="hero-arrow" style="left:144px"><svg width="10" height="12"><path d="M7 1L2 6l5 5" stroke="#fff" fill="none" stroke-width="1.4"/></svg></div>
  <div class="hero-arrow" style="left:787px"><svg width="10" height="12"><path d="M3 1l5 5-5 5" stroke="#fff" fill="none" stroke-width="1.4"/></svg></div>
  <div class="hero-caption">WE HAVE SPECIALISED ENGINEERS, TRAINED TO DO SPECIALISED WORK</div>
</section>

<section class="services">
  <h2 class="section-title">Our Services</h2>
  <div class="services-rule"></div>
  <div class="pager" style="left:790px;top:27px">
    <svg width="8" height="12"><path d="M6 1L1 6l5 5" stroke="#fff" fill="none"/></svg>
    <svg width="8" height="12"><path d="M2 1l5 5-5 5" stroke="#fff" fill="none"/></svg>
  </div>

  <div class="service-card" style="left:142px">
    <div class="service-icon"><svg width="52" height="44" viewBox="0 0 52 44"><path d="M10 38L34 12M18 38L42 10" stroke="#0aa84f" stroke-width="6" stroke-linecap="round"/><path d="M14 8l8 8-5 5-8-8z" fill="#0aa84f"/><path d="M36 4l10 6-4 4-8-4z" fill="#0aa84f"/></svg></div>
    <div class="service-label">ON-SITE SERVICE</div>
  </div>
  <div class="service-card" style="left:279px">
    <div class="service-icon"><svg width="54" height="44" viewBox="0 0 54 44"><rect x="6" y="4" width="30" height="22" rx="2" fill="none" stroke="#555" stroke-width="2.5"/><line x1="21" y1="26" x2="21" y2="32" stroke="#555" stroke-width="2.5"/><circle cx="36" cy="30" r="11" fill="#fff" stroke="#555" stroke-width="2.5"/><path d="M31 28h9l-3-3M41 32h-9l3 3" stroke="#555" fill="none" stroke-width="2"/></svg></div>
    <div class="service-label">REMOTE DESKTOP</div>
  </div>
  <div class="service-card" style="left:417px">
    <div class="service-icon"><svg width="54" height="46" viewBox="0 0 54 46"><path d="M8 4v12a10 10 0 0020 0V4M18 26v8a8 8 0 0016 0v-6" stroke="#555" stroke-width="2.5" fill="none"/><circle cx="34" cy="25" r="3.5" fill="none" stroke="#555" stroke-width="2"/><circle cx="40" cy="12" r="5" fill="none" stroke="#555" stroke-width="2.5" stroke-dasharray="3 2"/><circle cx="49" cy="7" r="3" fill="none" stroke="#555" stroke-width="2" stroke-dasharray="2 2"/></svg></div>
    <div class="service-label">MEDICAL IT SERVICE</div>
  </div>
  <div class="service-card" style="left:554px">
    <div class="service-icon"><svg width="54" height="44" viewBox="0 0 54 44"><rect x="6" y="4" width="34" height="28" fill="none" stroke="#555" stroke-width="3"/><path d="M11 24l7-8 6 6 5-7 6 5" stroke="#555" fill="none" stroke-width="2"/><circle cx="38" cy="30" r="7" fill="#fff" stroke="#555" stroke-width="3"/><line x1="43" y1="35" x2="50" y2="42" stroke="#555" stroke-width="4"/></svg></div>
    <div class="service-label">PHARMACY IT SERVICE</div>
  </div>
  <div class="service-card" style="left:692px">
    <div class="service-icon"><svg width="50" height="44" viewBox="0 0 50 44"><rect x="5" y="10" width="38" height="24" fill="none" stroke="#555" stroke-width="3"/><rect x="20" y="34" width="8" height="4" fill="#555"/><rect x="14" y="38" width="20" height="3" fill="#555"/><path d="M18 28l18-22 4 3-18 22z" fill="#555"/></svg></div>
    <div class="service-label">WEBSITE DESIGN</div>
  </div>
</section>
<div class="band-shadow"></div>

<section class="panel" style="left:142px">
  <h3 class="panel-head">About Velmora Systems</h3>
  <div class="about-photo" role="img" aria-label="Business team meeting around a laptop in an office"></div>
  <p class="about-text">Velmora Systems is an Adelaide based company with a single objective - to excel in the support and service of all computer and IT needs. We provide a high level of consulting services using the most experienced engineers at a reasonable and fair price. .......</p>
  <div class="tab-btn" style="left:60px;width:92px">READ MORE</div>
</section>
<div class="panel-shadow" style="left:142px"></div>

<section class="panel" style="left:373px">
  <h3 class="panel-head">What Our Clients Say</h3>
  <div class="quote" style="top:38px"><span class="q">“</span> Nonummy nibh uismod tincidunt ut laoreet<br>magna aliquam erat volutpat. Ut wisi enim ad<br>minim nonummy nibh euismod tincidunt <span class="q">”</span></div>
  <div class="quote-by" style="top:85px">Lena Marsh - Orvik</div>
  <div class="quote" style="top:106px"><span class="q">“</span> I have always found the team extremely<br>helpful with their advice over the phone. They<br>also have the ability to access our computers<br>remotely &amp; can rectify most problems quite<br>swiftly. <span class="q">”</span></div>
  <div class="quote-by" style="top:178px">Peter Calloway B.Pharm<br>Calloway Community Chemists, Angle Vale</div>
  <div class="tab-btn" style="left:60px;width:92px">READ MORE</div>
</section>
<div class="panel-shadow" style="left:373px"></div>

<section class="panel" style="left:606px">
  <h3 class="panel-head">Quick Contact</h3>
  <div class="field" style="top:37px">Name</div>
  <div class="field" style="top:70px">Email</div>
  <div class="field" style="top:103px">Phone</div>
  <div class="field" style="top:135px;height:60px">Message</div>
  <div class="tab-btn" style="left:64px;width:84px">SUBMIT</div>
</section>
<div class="panel-shadow" style="left:606px"></div>

<h2 class="section-title clients-title">Our Clients</h2>
<div class="pager" style="left:563px;top:959px">
  <svg width="8" height="12"><path d="M6 1L1 6l5 5" stroke="#555" fill="none"/></svg>
  <svg width="8" height="12"><path d="M2 1l5 5-5 5" stroke="#0aa84f" fill="none"/></svg>
</div>
<div class="rule" style="left:142px;top:976px;width:451px"></div>
<div class="client" style="left:142px"><i></i>Brevix</div>
<div class="client" style="left:282px"><i></i>Stratavo</div>
<div class="client" style="left:425px">Kelnor</div>
<div class="client" style="left:516px">Quadrix</div>

<h2 class="section-title remote-title">Remote Support</h2>
<div class="rule" style="left:609px;top:976px;width:209px"></div>
<div class="field" style="left:609px;top:986px;width:204px">Enter your 6 digit code</div>
<div class="connect">Connect Now</div>

<footer class="site-footer">
  <h4 class="foot-title" style="left:146px">Quick Links</h4>
  <ul class="quick-links">
    <li>Home</li><li>About Us</li><li>Services</li><li>Support</li><li>Clients</li><li>Contact Us</li><li>Terms &amp; Conditions</li>
  </ul>
  <h4 class="foot-title" style="left:286px;border:0">Newsletter</h4>
  <p class="news-text">Newsletter to Keep up with the latest in getting the most out of your web presence.</p>
  <div class="news-input">Enter Your Email</div>
  <div class="news-btn">Signup</div>

  <h4 class="foot-title" style="left:481px;width:147px">Contact Detail</h4>
  <div class="contact-row" style="top:40px">
    <svg width="9" height="13" viewBox="0 0 9 13"><path d="M4.5 0a4.5 4.5 0 014.5 4.5C9 8 4.5 13 4.5 13S0 8 0 4.5A4.5 4.5 0 014.5 0z" fill="#fff"/><circle cx="4.5" cy="4.5" r="1.8" fill="#0e3a66"/></svg>
    <span>Street Name, City Name<br>State Zipcode</span>
  </div>
  <div class="contact-row" style="top:78px;font-size:12px">
    <svg width="10" height="12" viewBox="0 0 10 12"><path d="M2 0c-2 1-2 4 0 7s4 5 6 5l1-2-2-2-1.5 1C4 8 2.5 6 2.5 4.5L4 3.5 3 0z" fill="#fff"/></svg>
    <span>123-456-7890</span>
  </div>
  <div class="contact-row" style="top:108px;font-size:8.5px">
    <svg width="11" height="8" viewBox="0 0 11 8"><rect width="11" height="8" fill="#fff"/><path d="M0 0l5.5 4.5L11 0" stroke="#0e3a66" fill="none"/></svg>
    <span>support@velmorasystems.example</span>
  </div>

  <div class="foot-brand"><span class="brand-dot"></span>Velmora Systems</div>
  <div class="follow">Follow Us On</div>
  <div class="social"><i></i><i></i><i></i><i></i></div>
</footer>

</body>
</html>
```